Stationery Design Project

We need a stationery design for our Norwegian trucking company. We have existed for about 15 years and our 12 drivers uses relatively new vehicles to transport goods around in northern Norway. Long distance routes with fresh fish og food transport is our main operations.

We have already made alogo that's printed on our trucks. The logo and a picture of our trucks is attached. I think the logo i crappy, but since its already in use, changing it is not an option in this round. Still using a better colour scheme in the overall stationery and more interesting fonts is possible (altso in the logo).

Company details:
Name: Kjelvraket AS
Organisation nr 873 615 309
Post adress: 8642 Raudvik

I like minimalism and simplicity. I am avalibly for questions in normal GMT working hours either here or on mail: ivar@fjordlast.no

Reason: Hi. Im extending the deadline because I needed some time to find a vector file of our logo. Sorry for the inconvenience

Hi, and thanks for all your interest in the project. Some updates:

-          I have decided to commit to using one of the designs. Some designer will get the payment.

-          I have extended the deadline with 24 hours since I needed some time to find our firms vector logo (a slow Swedish man was holding me up)

-          We will not choose a design before the deadline. No need to rush.

-          We have received a lot of great design and think there is a need to specified the product we want to make:

o   Business Card for all our employers. I just need the design and will duplicate with the correct numbers and name myself. The information on should be: Logo, employer’s name, Phone number, email, website, Postal number and address. Use this as a template: logo, Leif Brattvoll, 47382066, Leif@fjordlast.no,, fjordlast.no, 8642 Raudvik. The order and placement of the information is your creative decision.

o   Stickers to put on the goods we travel. On the sticker the should be the following information: Logo, phone number, Tekst and link: Fraktæ av Kjelvraket. Ke du syns? Fjordlast.no/tilbakemelding (this means: Handled by Kjelvraket. What do you think Fjordlast.no/feedback -à the link will be a feedback form). The placement the information and size is your creative decision with some stings: we have been thinking of using Drukko for printing and see that a size about 6x6 cm, 8x5 or something like that. (with 3000 copies our budget is 200 punds). Any suggestions of other suppliers are welcome. Drukko price calculator http://www.drukkolabelhouse.co.uk/digital-litho-printing/printing-labels-tags/stickers/

o   Letterhead with logo, address, phone number and organizational number.

o   Envelopes with logo,address, phone number and organizational number.

Have a nice day.

 

 

• Using the blue colour in the logo and using a similar graphic approch.

```html
<!DOCTYPE html>
<html lang="no">
<head>
<meta charset="utf-8">
<title>Kjelvraket AS – Stationery</title>
<link rel="stylesheet" href="https://fonts.googleapis.com/css2?family=Open+Sans:wght@400;600;700&display=swap">
<style>
:root{
  --bg:#26272b;
  --paper:#ffffff;
  --blue:#1a4eb0;
  --ink:#1b1b1d;
  --text:#333;
  --grey:#8a8a8a;
  --rule:#555;
}
*{box-sizing:border-box;margin:0;padding:0}
html,body{width:1200px;height:665px;overflow:hidden;background:var(--bg);font-family:"Open Sans",Arial,sans-serif;color:var(--text)}
.canvas{position:relative;width:1200px;height:665px}
.piece{position:absolute;background:var(--paper);overflow:hidden;box-shadow:0 2px 6px rgba(0,0,0,.5)}
.swoosh{position:absolute;left:0;bottom:0;width:100%;display:block}
.brand{font-weight:700;color:var(--blue);letter-spacing:-.2px;display:flex;align-items:center;gap:.3em;white-space:nowrap}
.brand::before{content:"";width:.55em;height:.55em;border-radius:50%;background:var(--blue)}
.addr{font-size:7.5px;line-height:1.35;color:var(--text)}
.contact{position:absolute;right:14px;bottom:7px;text-align:right;color:#fff;font-size:7px;line-height:1.45}

/* A4 sheets */
.sheet{top:25px;width:343px;height:442px}
.sheet .brand{position:absolute;left:22px;top:48px;font-size:19px}
.sheet .addr{position:absolute;right:24px;top:39px;text-align:right}
.fax{left:27px}
.letter{left:411px}
.fax-title{position:absolute;left:22px;top:76px;font-size:20px;color:var(--ink)}
.fax-fields{position:absolute;left:22px;top:106px;width:292px;display:grid;grid-template-columns:1fr 1fr;row-gap:8px}
.field{font-size:6.5px;color:var(--text);border-bottom:1px solid var(--rule);padding-bottom:1px;height:10px}
.fax-checks{position:absolute;left:22px;top:183px;width:292px;display:flex;justify-content:space-between;font-size:6.5px}
.check{display:flex;align-items:center;gap:4px}
.check::before{content:"";width:7px;height:7px;background:#c9c9c9}
.watermark{position:absolute;left:0;right:0;top:200px;text-align:center;font-size:40px;font-weight:700;color:var(--blue);opacity:.09}

/* compliment slip */
.slip{left:795px;top:28px;width:383px;height:166px}
.slip .brand{position:absolute;left:14px;top:30px;font-size:18px}
.slip .addr{position:absolute;left:14px;top:57px}

/* envelope */
.env-flap{position:absolute;left:799px;top:211px;width:380px;height:45px;background:var(--blue);border-radius:18px 18px 0 0;box-shadow:0 2px 6px rgba(0,0,0,.5)}
.env-flap .brand,.flap-brand{position:absolute;left:50%;top:50%;transform:translate(-50%,-50%) rotate(180deg);font-size:8px}
.env-flap .brand{color:#fff}
.env-flap .brand::before{background:#fff}
.envelope{left:798px;top:271px;width:381px;height:212px}
.flap-shape{position:absolute;left:0;top:0;width:100%;height:58px}
.flap-brand{top:22px}
.envelope .main-brand{position:absolute;left:14px;top:70px;font-size:20px}
.envelope .addr{position:absolute;left:16px;top:102px}
.envelope .web{position:absolute;right:18px;bottom:10px;color:#fff;font-size:6.5px;letter-spacing:3px}

/* cards */
.card{top:526px;width:150px;height:87px;border-radius:6px}
.card .brand{font-size:11px}
.card-front{left:31px}
.card-front .brand{position:absolute;left:10px;top:14px}
.card-front .person{position:absolute;left:11px;top:42px;font-size:5px;line-height:1.4}
.card-front .person strong{font-weight:400;font-size:5.5px}
.card-front .contact{right:6px;bottom:5px;font-size:3.8px}
.card-back,.card-dark{display:flex;flex-direction:column;align-items:center;justify-content:center;gap:12px}
.card-back{left:198px}
.card-dark{left:367px;background:var(--ink)}
.card-back .brand,.card-dark .brand{font-size:13px}
.card-web{font-size:4px;letter-spacing:1.5px;color:var(--grey)}

/* stickers */
.sticker{top:527px;width:127px;height:95px;border-radius:6px}
.sticker .brand{position:absolute;left:10px;top:7px;font-size:12px}
.sticker-msg{position:absolute;left:10px;top:32px;font-size:8px;line-height:1.25}
.sticker-foot{position:absolute;left:0;right:0;bottom:4px;text-align:center;font-size:3.8px}
.sticker-light{left:543px}
.sticker-light .sticker-msg{color:var(--blue)}
.sticker-light .sticker-foot{color:#fff}
.sticker-dark{left:689px;background:var(--blue)}
.sticker-dark .brand{color:#fff}
.sticker-dark .brand::before{background:#fff}
.sticker-dark .sticker-msg{color:#fff}
.sticker-dark .sticker-foot{color:var(--text)}
.sticker-round{left:856px;top:532px;width:95px;height:95px;border-radius:50%}
.sticker-round .brand{position:absolute;left:50%;top:14px;transform:translateX(-50%);font-size:9px}
.sticker-round .sticker-msg{left:0;right:0;top:30px;text-align:center;font-size:6.3px;color:var(--blue)}
.sticker-round .sticker-foot{bottom:14px;font-size:3.6px;color:#fff;line-height:1.3}
</style>
</head>
<body>
<svg width="0" height="0" style="position:absolute" aria-hidden="true">
  <defs>
    <symbol id="swoosh" viewBox="0 0 340 80" preserveAspectRatio="none">
      <path d="M0,72 C120,62 250,28 340,2 L340,19 C250,40 120,64 0,74 Z" fill="#1b1b1d"/>
      <path d="M0,77 C120,69 250,42 340,23 L340,80 L0,80 Z" fill="#1a4eb0"/>
    </symbol>
    <symbol id="swoosh-light" viewBox="0 0 340 80" preserveAspectRatio="none">
      <path d="M0,72 C120,62 250,28 340,2 L340,19 C250,40 120,64 0,74 Z" fill="#1b1b1d"/>
      <path d="M0,77 C120,69 250,42 340,23 L340,80 L0,80 Z" fill="#ffffff"/>
    </symbol>
  </defs>
</svg>

<main class="canvas">

  <section class="piece sheet fax" aria-label="Fax sheet">
    <div class="brand">Kjelvraket</div>
    <p class="addr">8642 Raudvik.<br>Org. nr. 873 615 309</p>
    <h1 class="fax-title">FAX</h1>
    <div class="fax-fields">
      <span class="field">To :</span><span class="field">From :</span>
      <span class="field">Fax :</span><span class="field">Page:</span>
      <span class="field">Phone :</span><span class="field">Date:</span>
      <span class="field">Re :</span><span class="field">CC:</span>
    </div>
    <div class="fax-checks">
      <span class="check">Urgent</span>
      <span class="check">For Review</span>
      <span class="check">Please Comment</span>
      <span class="check">Please Reply</span>
      <span>Please Recycle</span>
    </div>
    <svg class="swoosh" height="78"><use href="#swoosh"/></svg>
    <p class="contact">phone : 47382066<br>email : Leif@fjordlast.no<br>web : www.fjordlast.no</p>
  </section>

  <section class="piece sheet letter" aria-label="Letterhead">
    <div class="brand">Kjelvraket</div>
    <p class="addr">8642 Raudvik.<br>Org. nr. 873 615 309</p>
    <div class="watermark">Kjelvraket</div>
    <svg class="swoosh" height="78"><use href="#swoosh"/></svg>
    <p class="contact">phone : 47382066<br>email : Leif@fjordlast.no<br>web : www.fjordlast.no</p>
  </section>

  <section class="piece slip" aria-label="Compliment slip">
    <div class="brand">Kjelvraket</div>
    <p class="addr">8642 Raudvik.<br>Org. nr. 873 615 309</p>
    <svg class="swoosh" height="80"><use href="#swoosh"/></svg>
    <p class="contact">phone : 47382066<br>email : Leif@fjordlast.no<br>web : www.fjordlast.no</p>
  </section>

  <div class="env-flap" aria-label="Envelope flap"><span class="brand">Kjelvraket</span></div>

  <section class="piece envelope" aria-label="Envelope">
    <svg class="flap-shape" viewBox="0 0 381 58" preserveAspectRatio="none">
      <path d="M0,58 L0,20 Q0,0 30,0 L351,0 Q381,0 381,20 L381,58" fill="#fff" stroke="#d4d4d4"/>
    </svg>
    <span class="brand flap-brand">Kjelvraket</span>
    <div class="brand main-brand">Kjelvraket</div>
    <p class="addr">8642 Raudvik.<br>Org. nr. 873 615 309</p>
    <svg class="swoosh" height="90"><use href="#swoosh"/></svg>
    <p class="web">www.fjordlast.no</p>
  </section>

  <section class="piece card card-front" aria-label="Business card front">
    <div class="brand">Kjelvraket</div>
    <p class="person"><strong>Leif Brattvoll</strong><br>47382066<br>Leif@fjordlast.no<br>www.fjordlast.no</p>
    <svg class="swoosh" height="46"><use href="#swoosh"/></svg>
    <p class="contact">8642 Raudvik<br>Organisation nr 873 615 309</p>
  </section>

  <section class="piece card card-back" aria-label="Business card back">
    <div class="brand">Kjelvraket</div>
    <p class="card-web">www.fjordlast.no</p>
  </section>

  <section class="piece card card-dark" aria-label="Business card back, dark">
    <div class="brand">Kjelvraket</div>
    <p class="card-web">www.fjordlast.no</p>
  </section>

  <section class="piece sticker sticker-light" aria-label="Sticker, white">
    <div class="brand">Kjelvraket</div>
    <p class="sticker-msg">Tekst and link<br>Fraktæ av Kjelvraket<br>Ke du syns?</p>
    <svg class="swoosh" height="46"><use href="#swoosh"/></svg>
    <p class="sticker-foot">Fjordlast.no/tilbakemelding &nbsp;|&nbsp; phone : 47-382-066</p>
  </section>

  <section class="piece sticker sticker-dark" aria-label="Sticker, blue">
    <div class="brand">Kjelvraket</div>
    <p class="sticker-msg">Tekst and link<br>Fraktæ av Kjelvraket<br>Ke du syns?</p>
    <svg class="swoosh" height="30"><use href="#swoosh-light"/></svg>
    <p class="sticker-foot">Fjordlast.no/tilbakemelding &nbsp;|&nbsp; phone : 47-382-066</p>
  </section>

  <section class="piece sticker sticker-round" aria-label="Round sticker">
    <div class="brand">Kjelvraket</div>
    <p class="sticker-msg">Tekst and link<br>Fraktæ av Kjelvraket<br>Ke du syns?</p>
    <svg class="swoosh" height="38"><use href="#swoosh"/></svg>
    <p class="sticker-foot">Fjordlast.no/tilbakemelding<br>phone : 47-382-066</p>
  </section>

</main>
</body>
</html>
```